Wealth Education Business Needs Sharp Business Card Design

We need a business card design for a recently launched investor education business called Harbor Crest.

The final design should promote security, empowerment, self improvement and financial gain. The card will ideally promote the stature of the business.

For more information and colours please visit harborcrest.com.au

Target Market(s)

Corporate executives and high net worth individuals

Industry/Entity Type

Education

Contact Information for Business Card

```html
<!DOCTYPE html>
<html lang="en">
<head>
<meta charset="UTF-8">
<title>Harbor Crest — Business Card</title>
<link href="https://fonts.googleapis.com/css2?family=Exo+2:wght@400;500;600&display=swap" rel="stylesheet">
<style>
  :root {
    --bg: #e9e9eb;
    --card: #f7f7f8;
    --ink: #3b3a3c;
    --ink-soft: #4a4a4c;
    --blue: #1aa3dc;
    --teal: #0f7a78;
    --dark-band: #474548;
  }
  * { margin: 0; padding: 0; box-sizing: border-box; }
  html, body {
    width: 1200px; height: 900px; overflow: hidden;
    background: var(--bg);
    font-family: "Exo 2", sans-serif;
  }
  .canvas {
    position: relative; width: 1200px; height: 900px;
  }
  .card {
    position: absolute; left: 100px; top: 164px;
    width: 1000px; height: 572px;
    border-radius: 52px;
    background: linear-gradient(160deg, #ffffff 0%, var(--card) 60%, #ececee 100%);
    overflow: hidden;
    box-shadow: 0 18px 40px rgba(0,0,0,0.18);
  }
  .card-waves { position: absolute; inset: 0; width: 100%; height: 100%; }
  .contact-list {
    position: absolute; left: 48px; top: 118px;
    list-style: none;
  }
  .contact-item {
    display: flex; align-items: center; gap: 16px;
    height: 38px;
    font-size: 23px; color: var(--ink-soft); letter-spacing: 1px;
  }
  .contact-item svg { width: 22px; height: 22px; flex: none; }
  .contact-item.small { font-size: 20px; letter-spacing: 0.3px; }
  .brand {
    position: absolute; right: 52px; top: 196px;
    display: flex; align-items: center; gap: 18px;
  }
  .brand-mark { width: 34px; height: 34px; background: var(--teal); }
  .brand-name {
    font-size: 62px; font-weight: 500; color: var(--ink);
    letter-spacing: 9px; text-transform: uppercase; line-height: 1;
  }
  .person {
    position: absolute; right: 110px; top: 338px; text-align: right;
  }
  .person-name {
    font-size: 31px; font-weight: 500; color: var(--blue);
    letter-spacing: 2px; text-transform: uppercase; line-height: 1.1;
  }
  .person-role {
    font-size: 20px; color: var(--ink); letter-spacing: 2px;
    text-transform: uppercase; margin-top: 4px;
  }
</style>
</head>
<body>
<div class="canvas">
  <section class="card">
    <svg class="card-waves" viewBox="0 0 1000 572" preserveAspectRatio="none" aria-hidden="true">
      <path fill="var(--teal)" d="M0 360 C 280 430, 640 470, 1000 355 L1000 376 C 640 492, 280 458, 0 386 Z"/>
      <path fill="var(--dark-band)" d="M0 398 C 280 462, 600 494, 1000 388 L1000 400 C 600 508, 280 478, 0 414 Z"/>
      <path fill="var(--dark-band)" d="M0 428 C 300 496, 640 520, 1000 410 L1000 572 L0 572 Z"/>
    </svg>

    <ul class="contact-list">
      <li class="contact-item">
        <svg viewBox="0 0 24 24"><path fill="var(--blue)" d="M6.6 10.8a15 15 0 0 0 6.6 6.6l2.2-2.2a1 1 0 0 1 1-.25 11.4 11.4 0 0 0 3.6.57 1 1 0 0 1 1 1V20a1 1 0 0 1-1 1A17 17 0 0 1 3 4a1 1 0 0 1 1-1h3.5a1 1 0 0 1 1 1c0 1.25.2 2.45.57 3.6a1 1 0 0 1-.25 1z"/></svg>
        012 345 6789
      </li>
      <li class="contact-item">
        <svg viewBox="0 0 24 24"><rect x="6" y="2" width="12" height="20" rx="2" fill="var(--blue)"/><rect x="8" y="5" width="8" height="12" fill="#fff"/></svg>
        012 345 6789
      </li>
      <li class="contact-item">
        <svg viewBox="0 0 24 24"><rect x="3" y="9" width="18" height="12" rx="1.5" fill="var(--blue)"/><rect x="7" y="3" width="10" height="8" fill="var(--blue)"/><rect x="9" y="5" width="6" height="4" fill="#fff"/></svg>
        012 345 6789
      </li>
      <li class="contact-item small">
        <svg viewBox="0 0 24 24"><rect x="2" y="5" width="20" height="14" rx="1.5" fill="var(--blue)"/><path d="M3 6l9 7 9-7" stroke="#fff" stroke-width="1.6" fill="none"/></svg>
        urname@email.com
      </li>
      <li class="contact-item small">
        <svg viewBox="0 0 24 24"><circle cx="12" cy="12" r="9.5" fill="var(--blue)"/><g stroke="#fff" stroke-width="1.2" fill="none"><ellipse cx="12" cy="12" rx="4" ry="9.5"/><path d="M2.5 12h19M4 7.5h16M4 16.5h16"/></g></svg>
        www.urwebsitename.com
      </li>
    </ul>

    <div class="brand">
      <span class="brand-mark"></span>
      <span class="brand-name">Harbor Crest</span>
    </div>

    <div class="person">
      <p class="person-name">Daniel Reeves</p>
      <p class="person-role">Financial Advisor</p>
    </div>
  </section>
</div>
</body>
</html>
```